Phuket Thailand - Rental Villa Website

I have a villa for rent in Thailand and require a website - i need to demo pictures/walk through video, local attractions, villa facilities description plus seaonal rates and online booking.

Industry/Entity Type

Rental

Coding

Coded - Design and coding required

```html
<!DOCTYPE html>
<html lang="en">
<head>
<meta charset="utf-8">
<title>Palm Cove Villas</title>
<link rel="stylesheet" href="https://fonts.googleapis.com/css2?family=Raleway:wght@400;500;600;700&family=Arimo:wght@400;700&display=swap">
<style>
:root{
  --teal:#31b3a5;
  --teal-dark:#26968a;
  --ink:#333333;
  --muted:#7a7a7a;
  --line:#e2e2e2;
  --panel:#f2f2f2;
  --navy:#2f3a48;
  --footer:#232323;
  --footer-text:#9a9a9a;
  --white:#ffffff;
}
*{box-sizing:border-box;margin:0;padding:0}
html,body{width:1200px;height:2347px;overflow:hidden;background:var(--white)}
body{position:relative;font-family:"Arimo",Arial,sans-serif;color:var(--ink)}
.abs{position:absolute}
.heading{font-family:"Raleway",sans-serif}

/* header */
.site-header{left:0;top:0;width:1200px;height:106px;border-top:4px solid var(--teal);background:var(--white)}
.brand{left:99px;top:22px;display:flex;align-items:center;gap:10px}
.brand-mark{width:30px;height:30px;background:var(--teal)}
.brand-name{font-family:"Raleway",sans-serif;font-weight:700;font-size:22px;color:var(--navy)}
.main-nav{right:100px;top:38px;display:flex;gap:10px;align-items:center}
.main-nav a{font-family:"Raleway",sans-serif;font-size:13px;font-weight:600;color:var(--ink);text-decoration:none;padding:8px 14px;letter-spacing:.3px}
.main-nav a:nth-child(n+2){margin-left:14px}
.main-nav a.is-active{background:var(--teal);color:var(--white);box-shadow:0 2px 3px rgba(0,0,0,.25)}

/* hero */
.hero{left:0;top:106px;width:1200px;height:548px;background:linear-gradient(160deg,#6d7a4a 0%,#9ea3a6 30%,#6a5b55 55%,#8a756c 80%,#4f5a3c 100%)}
.hero-arrow{top:248px;width:48px;height:48px;border:2px solid rgba(255,255,255,.6);border-radius:50%}
.hero-arrow.prev{left:32px}
.hero-arrow.next{left:1114px}
.search-panel{left:124px;top:433px;width:953px;height:177px;background:var(--white);box-shadow:0 1px 4px rgba(0,0,0,.25)}
.search-step{top:20px}
.step-title{font-family:"Raleway",sans-serif;font-size:13px;color:var(--ink)}
.step-title b{color:var(--teal);font-size:17px;font-weight:700;margin-right:4px}
.step-label{font-size:13px;color:var(--ink);font-family:"Raleway",sans-serif}
.field{height:32px;border:1px solid #cfcfcf;border-radius:16px;font-size:10px;color:#999;padding:9px 12px;background:var(--white)}
.field svg{position:absolute;right:10px;top:10px}
.step-sep{top:20px;width:1px;height:135px;background:var(--line)}
.booking-btn{left:393px;top:144px;width:166px;height:34px;border-radius:17px;background:var(--teal);color:var(--white);font-family:"Raleway",sans-serif;font-size:14px;font-weight:500;text-align:center;line-height:34px}

/* featured video */
.video-frame{left:99px;top:717px;width:461px;height:288px;border:1px solid #d6d6d6;padding:5px;background:var(--white)}
.video-still{width:100%;height:100%;background:linear-gradient(170deg,#8c949b 0%,#6e7d6c 40%,#4f4a3d 70%,#6e6e66 100%);position:relative}
.play-btn{left:195px;top:108px;width:62px;height:62px;border-radius:50%;background:rgba(40,40,40,.55)}
.video-bar{left:0;bottom:0;width:100%;height:36px;background:rgba(20,20,20,.7)}
.section-title{font-family:"Raleway",sans-serif;font-weight:700;font-size:25px;color:var(--teal);letter-spacing:.5px}
.body-text{font-size:10.5px;line-height:20px;color:var(--muted)}
.btn{background:var(--teal);color:var(--white);font-family:"Raleway",sans-serif;font-size:17px;text-align:center;box-shadow:0 3px 0 var(--teal-dark)}
.divider{left:99px;width:1003px;height:1px;background:var(--line)}

/* rates */
.plain-title{font-family:"Raleway",sans-serif;font-size:19px;color:var(--ink);letter-spacing:.3px}
.pager{top:1080px;width:17px;height:17px;background:#b0b0b0}
.rate-card{top:1121px;width:319px;height:350px;border:1px solid #ddd;box-shadow:0 1px 3px rgba(0,0,0,.12);background:var(--white)}
.rate-photo{left:7px;top:9px;width:303px;height:183px}
.price-tag{right:8px;top:9px;height:30px;display:flex}
.price-tag span{background:var(--teal);color:var(--white);font-family:"Raleway",sans-serif;font-weight:700;font-size:15px;padding:0 8px;line-height:30px}
.price-tag i{width:30px;background:var(--navy);display:block;position:relative}
.stats{left:7px;top:192px;width:303px;height:28px;background:var(--panel);display:flex;align-items:center;gap:24px;padding-left:10px;font-size:9.5px;color:var(--ink)}
.stats span{display:flex;align-items:center;gap:6px}
.card-text{left:8px;top:232px;width:300px;font-size:10.5px;line-height:20px;color:var(--muted)}
.card-foot{left:0;bottom:0;width:100%;height:42px;background:var(--panel);display:flex;align-items:center;gap:12px;padding-left:14px;font-size:12px;color:var(--muted);font-family:"Raleway",sans-serif}

/* attractions */
.attraction{width:224px;height:141px}
.attraction .caption{position:absolute;left:0;bottom:0;width:100%;height:36px;background:rgba(20,20,20,.7);color:var(--white);font-family:"Raleway",sans-serif;font-size:14px;text-align:center;line-height:36px}

/* map */
.map{left:0;top:1898px;width:1200px;height:266px;background:linear-gradient(100deg,#dfe6cf 0%,#ecebe3 30%,#e8e4d8 60%,#efe9d8 100%)}

/* footer */
.site-footer{left:0;top:2164px;width:1200px;height:183px;background:var(--footer)}
.foot-title{font-family:"Raleway",sans-serif;font-size:16px;color:#e0e0e0}
.contact-item{display:flex;gap:14px;font-size:10px;color:var(--footer-text);line-height:20px}
.contact-icon{width:28px;height:28px;border:1px solid #555;border-radius:50%;flex:none;display:flex;align-items:center;justify-content:center}
.social{top:2226px;width:24px;height:24px}
.foot-rule{left:0;top:2285px;width:1200px;height:1px;background:#333}
.copyright{left:0;top:2307px;width:1200px;text-align:center;font-size:10px;color:var(--footer-text)}
</style>
</head>
<body>

<header class="site-header abs">
  <div class="brand abs"><span class="brand-mark"></span><span class="brand-name">Palm Cove Villas</span></div>
  <nav class="main-nav abs">
    <a class="is-active">HOME</a><a>ABOUT US</a><a>PROPERTIES</a><a>AGENTS</a><a>BLOG</a><a>FAQ</a><a>CONTACT</a>
  </nav>
</header>

<section class="hero abs" role="img" aria-label="Villa exterior with shingled curved roof among tropical trees">
  <span class="hero-arrow prev abs"><svg width="44" height="44" viewBox="0 0 44 44"><path d="M25 14l-8 8 8 8" fill="none" stroke="#fff" stroke-width="2"/></svg></span>
  <span class="hero-arrow next abs"><svg width="44" height="44" viewBox="0 0 44 44"><path d="M19 14l8 8-8 8" fill="none" stroke="#fff" stroke-width="2"/></svg></span>
</section>

<form class="search-panel abs">
  <div class="search-step abs" style="left:20px">
    <div class="step-title"><b>01</b>What?</div>
    <div class="step-label abs" style="top:38px;left:2px">Search Villa</div>
    <div class="field abs" style="top:64px;left:-6px;width:192px">Enter Any Key Word :
      <svg width="11" height="11" viewBox="0 0 11 11"><circle cx="4.5" cy="4.5" r="3.5" fill="none" stroke="#777" stroke-width="1.3"/><path d="M7 7l3 3" stroke="#777" stroke-width="1.3"/></svg></div>
  </div>
  <div class="step-sep abs" style="left:222px"></div>
  <div class="search-step abs" style="left:248px">
    <div class="step-title"><b>02</b>Where?</div>
    <div class="step-label abs" style="top:38px;left:0;white-space:nowrap">Your Destination</div>
    <div class="field abs" style="top:64px;left:-6px;width:208px;white-space:nowrap">City,region,district or specific villa</div>
  </div>
  <div class="step-sep abs" style="left:474px"></div>
  <div class="search-step abs" style="left:502px">
    <div class="step-title"><b>03</b>When?</div>
    <div class="step-label abs" style="top:38px;left:0;white-space:nowrap">Check-in-Date</div>
    <div class="step-label abs" style="top:38px;left:107px;white-space:nowrap">Check-Out-Date</div>
    <div class="field abs" style="top:64px;left:-5px;width:95px"><svg width="10" height="10" viewBox="0 0 10 10"><rect x="1" y="2" width="8" height="7" fill="none" stroke="#999"/><path d="M1 4h8" stroke="#999"/></svg></div>
    <div class="field abs" style="top:64px;left:103px;width:95px"><svg width="10" height="10" viewBox="0 0 10 10"><rect x="1" y="2" width="8" height="7" fill="none" stroke="#999"/><path d="M1 4h8" stroke="#999"/></svg></div>
  </div>
  <div class="step-sep abs" style="left:720px"></div>
  <div class="search-step abs" style="left:742px">
    <div class="step-title"><b>03</b>Who?</div>
    <div class="step-label abs" style="top:38px;left:2px">Room</div>
    <div class="step-label abs" style="top:38px;left:78px">Adults</div>
    <div class="step-label abs" style="top:38px;left:144px;white-space:nowrap">Children</div>
    <div class="field abs" style="top:64px;left:-4px;width:62px"><svg width="8" height="10" viewBox="0 0 8 10"><path d="M1 4l3-3 3 3M1 6l3 3 3-3" fill="none" stroke="#777"/></svg></div>
    <div class="field abs" style="top:64px;left:64px;width:62px"><svg width="8" height="10" viewBox="0 0 8 10"><path d="M1 4l3-3 3 3M1 6l3 3 3-3" fill="none" stroke="#777"/></svg></div>
    <div class="field abs" style="top:64px;left:132px;width:62px"><svg width="8" height="10" viewBox="0 0 8 10"><path d="M1 4l3-3 3 3M1 6l3 3 3-3" fill="none" stroke="#777"/></svg></div>
  </div>
  <div class="booking-btn abs">Booking Now</div>
</form>

<section class="featured-video">
  <div class="video-frame abs">
    <div class="video-still" role="img" aria-label="Walk-through video of the timber pergola terrace overlooking a lake and hills">
      <span class="play-btn abs"><svg width="62" height="62" viewBox="0 0 62 62"><path d="M25 19l18 12-18 12z" fill="#fff" opacity=".85"/></svg></span>
      <div class="video-bar abs">
        <svg width="449" height="36" viewBox="0 0 449 36">
          <rect x="10" y="8" width="22" height="20" rx="2" fill="#111"/>
          <rect x="18" y="13" width="2" height="10" fill="#fff"/><rect x="22" y="13" width="2" height="10" fill="#fff"/>
          <text x="96" y="22" font-size="9" fill="#ddd" font-family="Arimo,sans-serif">01:46</text>
          <rect x="124" y="17" width="220" height="3" fill="#555"/><rect x="124" y="17" width="48" height="3" fill="#ddd"/>
          <text x="350" y="22" font-size="9" fill="#ddd" font-family="Arimo,sans-serif">02:27</text>
          <rect x="382" y="8" width="20" height="20" rx="2" fill="#111"/><rect x="408" y="8" width="20" height="20" rx="2" fill="#111"/>
          <path d="M387 13h4M387 13v4M397 23h-4M397 23v-4" stroke="#fff"/>
          <path d="M413 16h3l3-3v10l-3-3h-3z" fill="#fff"/>
        </svg>
      </div>
    </div>
  </div>
  <h2 class="section-title abs" style="left:615px;top:718px">FEATURED VIDEO</h2>
  <p class="body-text abs" style="left:617px;top:768px;width:410px">It is a long established fact that a reader will be distracted by the readable content of a page when looking at its layout. The point of using Lorem Ipsum is that it has a more-or-less normal distribution of letters, as opposed to using 'Content here, content here', making it look like readable English.</p>
  <p class="body-text abs" style="left:617px;top:878px;width:410px">The point of using Lorem Ipsum is that it has a more-or-less normal distribution of letters, 'Content here, content here', making it look like readable English.</p>
  <div class="btn abs" style="left:617px;top:956px;width:170px;height:40px;line-height:40px">READ MORE</div>
</section>

<div class="divider abs" style="top:1045px"></div>

<section class="rates">
  <h2 class="plain-title abs" style="left:97px;top:1077px">FACILITIES &nbsp;SEASONAL RATES</h2>
  <span class="pager abs" style="left:1063px"><svg width="17" height="17" viewBox="0 0 17 17"><path d="M10 5l-3 3.5 3 3.5" fill="none" stroke="#fff"/></svg></span>
  <span class="pager abs" style="left:1081px"><svg width="17" height="17" viewBox="0 0 17 17"><path d="M7 5l3 3.5-3 3.5" fill="none" stroke="#fff"/></svg></span>

  <article class="rate-card abs" style="left:99px">
    <div class="rate-photo abs" role="img" aria-label="Pergola terrace by the lake" style="background:linear-gradient(170deg,#8e979c,#5f6b57 55%,#7d7a70)"></div>
    <div class="price-tag abs"><span>$5000,00</span><i><svg width="30" height="30" viewBox="0 0 30 30"><path d="M9 9h7l6 6-7 7-6-6z" fill="#fff"/><circle cx="12" cy="12" r="1.3" fill="#2f3a48"/></svg></i></div>
    <div class="stats abs">
      <span><svg width="12" height="11" viewBox="0 0 12 11"><path d="M1 6l5-5 5 5v5H7V8H5v3H1z" fill="#333"/></svg>20,000 Acres</span>
      <span><svg width="14" height="9" viewBox="0 0 14 9"><path d="M0 0h2v5h12v4h-2V7H2v2H0z M3 2h3v2H3z M7 2h6v2H7z" fill="#333"/></svg>4 Bedrooms</span>
      <span><svg width="8" height="12" viewBox="0 0 8 12"><circle cx="4" cy="2" r="1.8" fill="#333"/><path d="M1 4h6v4H6v4H2V8H1z" fill="#333"/></svg>3 Bathrooms</span>
    </div>
    <p class="card-text abs">It is a long established fact that a reader will be distracted by the readable content of a page when looking at its layout. The point of of letters, as opposed to using</p>
    <div class="card-foot abs"><svg width="10" height="14" viewBox="0 0 10 14"><path d="M5 0a5 5 0 015 5c0 4-5 9-5 9S0 9 0 5a5 5 0 015-5z" fill="#999"/><circle cx="5" cy="5" r="2" fill="#f2f2f2"/></svg>Contrary to popular belief,not simply random</div>
  </article>

  <article class="rate-card abs" style="left:441px">
    <div class="rate-photo abs" role="img" aria-label="Bedroom with double bed and wall art" style="background:linear-gradient(160deg,#6d6460,#4a3f3a 50%,#a29a97)"></div>
    <div class="price-tag abs"><span>$5000,00</span><i><svg width="30" height="30" viewBox="0 0 30 30"><path d="M9 9h7l6 6-7 7-6-6z" fill="#fff"/><circle cx="12" cy="12" r="1.3" fill="#2f3a48"/></svg></i></div>
    <div class="stats abs">
      <span><svg width="12" height="11" viewBox="0 0 12 11"><path d="M1 6l5-5 5 5v5H7V8H5v3H1z" fill="#333"/></svg>20,000 Acres</span>
      <span><svg width="14" height="9" viewBox="0 0 14 9"><path d="M0 0h2v5h12v4h-2V7H2v2H0z M3 2h3v2H3z M7 2h6v2H7z" fill="#333"/></svg>4 Bedrooms</span>
      <span><svg width="8" height="12" viewBox="0 0 8 12"><circle cx="4" cy="2" r="1.8" fill="#333"/><path d="M1 4h6v4H6v4H2V8H1z" fill="#333"/></svg>3 Bathrooms</span>
    </div>
    <p class="card-text abs">It is a long established fact that a reader will be distracted by the readable content of a page when looking at its layout. The point of of letters, as opposed to using</p>
    <div class="card-foot abs"><svg width="10" height="14" viewBox="0 0 10 14"><path d="M5 0a5 5 0 015 5c0 4-5 9-5 9S0 9 0 5a5 5 0 015-5z" fill="#999"/><circle cx="5" cy="5" r="2" fill="#f2f2f2"/></svg>Contrary to popular belief,not simply random</div>
  </article>

  <article class="rate-card abs" style="left:784px">
    <div class="rate-photo abs" role="img" aria-label="Infinity swimming pool" style="background:linear-gradient(170deg,#9aa49a,#5f8a86 45%,#3e6d6b)"></div>
    <div class="price-tag abs"><span>$5000,00</span><i><svg width="30" height="30" viewBox="0 0 30 30"><path d="M9 9h7l6 6-7 7-6-6z" fill="#fff"/><circle cx="12" cy="12" r="1.3" fill="#2f3a48"/></svg></i></div>
    <div class="stats abs">
      <span><svg width="12" height="11" viewBox="0 0 12 11"><path d="M1 6l5-5 5 5v5H7V8H5v3H1z" fill="#333"/></svg>20,000 Acres</span>
      <span><svg width="14" height="9" viewBox="0 0 14 9"><path d="M0 0h2v5h12v4h-2V7H2v2H0z M3 2h3v2H3z M7 2h6v2H7z" fill="#333"/></svg>4 Bedrooms</span>
      <span><svg width="8" height="12" viewBox="0 0 8 12"><circle cx="4" cy="2" r="1.8" fill="#333"/><path d="M1 4h6v4H6v4H2V8H1z" fill="#333"/></svg>3 Bathrooms</span>
    </div>
    <p class="card-text abs">It is a long established fact that a reader will be distracted by the readable content of a page when looking at its layout. The point of of letters, as opposed to using</p>
    <div class="card-foot abs"><svg width="10" height="14" viewBox="0 0 10 14"><path d="M5 0a5 5 0 015 5c0 4-5 9-5 9S0 9 0 5a5 5 0 015-5z" fill="#999"/><circle cx="5" cy="5" r="2" fill="#f2f2f2"/></svg>Contrary to popular belief,not simply random</div>
  </article>
</section>

<div class="divider abs" style="top:1504px"></div>

<section class="attractions">
  <h2 class="plain-title abs" style="left:99px;top:1535px">LOCAL ATTRACTIONS</h2>
  <p class="body-text abs" style="left:99px;top:1572px;width:490px">It is a long established fact that a reader will be distracted by the readable content of a page when looking at its layout. The point of using Lorem Ipsum is that it has a more-or-less normal distribution of letters, as opposed to using 'Content here, content here', making it look like readable English. Many and a search for 'lorem ipsum' will uncover many web sites still in their infancy simply dummy text of the printing and type-setting industry. Lorem Ipsum has been the industry's standard dummy text ever &nbsp;took a galley of type and scrambled it to make a type specimen book.</p>
  <p class="body-text abs" style="left:99px;top:1710px;width:490px">Making it look like readable English. Many and a search for 'lorem ipsum' will uncover many web sites still in their infancy simply dummy text of the printing and typesetting industry. Lorem Ipsum has been the &nbsp;took a galley of type and scrambled it to make a type specimen book.</p>
  <div class="btn abs" style="left:99px;top:1793px;width:172px;height:40px;line-height:40px">VIEW ALL</div>

  <figure class="attraction abs" style="left:624px;top:1537px;background:linear-gradient(160deg,#8a9590,#6b5e58 55%,#4c5a3c)" role="img" aria-label="Villa roof and garden"><figcaption class="caption">Neque porro quisquam</figcaption></figure>
  <figure class="attraction abs" style="left:873px;top:1537px;background:linear-gradient(160deg,#a8a296,#6e5443 50%,#8a8e80)" role="img" aria-label="Covered terrace with parasols"><figcaption class="caption">Neque porro quisquam</figcaption></figure>
  <figure class="attraction abs" style="left:624px;top:1695px;background:linear-gradient(170deg,#a7aea6,#5f8b86 50%,#3f6b68)" role="img" aria-label="Swimming pool"><figcaption class="caption">Neque porro quisquam</figcaption></figure>
  <figure class="attraction abs" style="left:873px;top:1695px;background:linear-gradient(170deg,#8e979c,#5f6b57 55%,#7d7a70)" role="img" aria-label="Lakeside pergola"><figcaption class="caption">Neque porro quisquam</figcaption></figure>
</section>

<div class="map abs" role="img" aria-label="Street map showing the villa location"></div>

<footer class="site-footer abs">
  <h3 class="foot-title abs" style="left:117px;top:26px">Contact us</h3>
  <div class="contact-item abs" style="left:113px;top:58px;width:240px">
    <span class="contact-icon"><svg width="8" height="12" viewBox="0 0 10 14"><path d="M5 0a5 5 0 015 5c0 4-5 9-5 9S0 9 0 5a5 5 0 015-5z" fill="#888"/><circle cx="5" cy="5" r="2" fill="#232323"/></svg></span>
    <span>Address : 8405 Lorem Ipsum Dummy<br>Content</span>
  </div>
  <div class="contact-item abs" style="left:430px;top:58px">
    <span class="contact-icon"><svg width="12" height="12" viewBox="0 0 12 12"><path d="M2 1l2 0 1 3-1.5 1a7 7 0 003.5 3.5L8 7l3 1v2c0 1-1 1-1 1C5 11 1 7 1 2c0 0 0-1 1-1z" fill="#888"/></svg></span>
    <span>Phone : (000)-121-1231</span>
  </div>
  <div class="contact-item abs" style="left:648px;top:58px">
    <span class="contact-icon"><svg width="12" height="9" viewBox="0 0 12 9"><rect x=".5" y=".5" width="11" height="8" fill="none" stroke="#888"/><path d="M.5 .5l5.5 4.5 5.5-4.5" fill="none" stroke="#888"/></svg></span>
    <span>Email : info@palmcovevillas.com</span>
  </div>
  <h3 class="foot-title abs" style="left:929px;top:26px">Follow us on</h3>
</footer>
<span class="social abs" style="left:930px;background:#3b5a9a" aria-label="Social profile 1"></span>
<span class="social abs" style="left:964px;background:#3fa8e0" aria-label="Social profile 2"></span>
<span class="social abs" style="left:998px;background:#d34836" aria-label="Social profile 3"></span>
<span class="social abs" style="left:1032px;background:#f26c3a" aria-label="Social profile 4"></span>
<div class="foot-rule abs"></div>
<p class="copyright abs">© Copyright2015 Palm Cove Villas. All rights reserved.</p>

</body>
</html>
```